"Vine Hollow Excursions" is a top notch Santa Barbara County Wine Tour company.

We provide scenic, boutique and custom wine tours. I need the card to be clean and classy. I will provide our logo. I would like the logo to cover the back side of the card as an option and would like to see a couple color options other then our signature green and gold. I would like to see some creative options and let the designers come up with options.
I need cards for myself and my team. The final design should communicate "An authentic and boutique wine tour experience"
Please use my website for reference www.vinehollowexcursions.example

Target Market(s)

We have a wide range of clients from millennials to baby boomers

Industry/Entity Type

Tour

Contact Information for Business Card

Contact info:
Dale Morton
805-219-6384
info@vinehollowexcursions.example
vinehollowexcursions.example

Colors

Designer to choose colors to be used in the design.

Requirements
Must have
• my logo
Nice to have
• *I would like to have the backside side with the logo and the company statement
• "An authentic and boutique wine tour experience" as an option.
• *I would also like to see what the designers can create!
• *I would like to see an option that incorporates or social: instagram, yelp, trip advisor
Should not have
• I do not want it too busy.

```html
<!DOCTYPE html>
<html lang="en">
<head>
<meta charset="utf-8">
<title>Vine Hollow Excursions – Business Card</title>
<link href="https://fonts.googleapis.com/css2?family=Roboto:wght@400;500&family=Roboto+Condensed:wght@700&display=swap" rel="stylesheet">
<style>
  :root {
    --bg: #e9e9e6;
    --card-front: #f3f3f1;
    --green: #276845;
    --gold: #9a7f62;
    --text-grey: #555555;
    --rule: #8a8a8a;
    --white: #ffffff;
    --badge-tan: #c9a57a;
    --badge-green: #5f9a3a;
    --badge-red: #d93a2e;
  }
  * { margin: 0; padding: 0; box-sizing: border-box; }
  html, body {
    width: 1200px; height: 960px; overflow: hidden;
    background: var(--bg);
    font-family: "Roboto", Arial, sans-serif;
  }
  .canvas { position: relative; width: 1200px; height: 960px; }

  .card {
    position: absolute;
    width: 600px; height: 343px;
    box-shadow: 0 2px 6px rgba(0,0,0,0.18);
    overflow: hidden;
  }

  /* Front */
  .card-front { left: 314px; top: 113px; background: var(--card-front); }
  .brand-name {
    position: absolute; left: 36px; top: 100px;
    font-family: "Roboto", Arial, sans-serif;
    font-weight: 500; font-size: 22px; letter-spacing: 0.5px;
    color: var(--gold);
  }
  .brand-dot {
    position: absolute; left: 36px; top: 62px;
    width: 26px; height: 26px; background: var(--green);
  }
  .person-name {
    position: absolute; right: 34px; top: 110px;
    font-family: "Roboto Condensed", "Arial Narrow", sans-serif;
    font-weight: 700; font-size: 22px; color: var(--green);
  }
  .name-rule {
    position: absolute; left: 250px; right: 34px; top: 142px;
    height: 1px; background: var(--rule);
  }
  .edge-tab {
    position: absolute; right: 0; top: 107px;
    width: 9px; height: 32px; background: var(--green);
    border-radius: 5px 0 0 5px;
  }
  .contact-list {
    position: absolute; left: 38px; top: 253px;
    list-style: none; font-size: 14.5px; color: var(--text-grey);
  }
  .contact-list li { display: flex; align-items: center; height: 19px; }
  .contact-list svg { width: 13px; height: 13px; margin-right: 7px; fill: var(--green); }

  /* Back */
  .card-back { left: 311px; top: 472px; background: var(--green); }
  .social-badges {
    position: absolute; right: 30px; top: 29px; display: flex; gap: 4px;
  }
  .social-badge { width: 32px; height: 32px; border-radius: 5px; }
  .social-badge.tan { background: var(--badge-tan); }
  .social-badge.green { background: var(--badge-green); }
  .social-badge.red { background: var(--badge-red); }
  .back-brand {
    position: absolute; left: 0; right: 0; top: 150px;
    text-align: center;
    font-family: "Roboto", Arial, sans-serif;
    font-weight: 500; font-size: 30px; letter-spacing: 1px;
    color: var(--white);
  }
  .tagline {
    position: absolute; left: 148px; top: 293px;
    font-size: 14.5px; color: var(--white);
  }
</style>
</head>
<body>
<main class="canvas">
  <section class="card card-front" aria-label="Card front">
    <span class="brand-dot"></span>
    <div class="brand-name">Vine Hollow Excursions</div>
    <div class="person-name">DALE MORTON</div>
    <div class="name-rule"></div>
    <div class="edge-tab"></div>
    <ul class="contact-list">
      <li>
        <svg viewBox="0 0 24 24" aria-hidden="true"><path d="M6.6 10.8a15 15 0 0 0 6.6 6.6l2.2-2.2c.3-.3.7-.4 1-.2 1.1.4 2.3.6 3.6.6.6 0 1 .4 1 1V20c0 .6-.4 1-1 1A17 17 0 0 1 3 4c0-.6.4-1 1-1h3.5c.6 0 1 .4 1 1 0 1.3.2 2.5.6 3.6.1.3 0 .7-.2 1z"/></svg>
        805-219-6384
      </li>
      <li>
        <svg viewBox="0 0 24 24" aria-hidden="true"><path d="M2 5h20v14H2z M2 5l10 7 10-7" fill="var(--green)"/><path d="M3 6l9 6.3L21 6" fill="none" stroke="#f3f3f1" stroke-width="1.6"/></svg>
        info@vinehollowexcursions.example
      </li>
      <li>
        <svg viewBox="0 0 24 24" aria-hidden="true"><circle cx="12" cy="12" r="10"/><path d="M6 8c2 0 3 1 3 3s2 2 2 4-1 3-1 5M14 3c0 2 1 3 3 3s3 2 3 4" fill="none" stroke="#f3f3f1" stroke-width="1.6"/></svg>
        vinehollowexcursions.example
      </li>
    </ul>
  </section>

  <section class="card card-back" aria-label="Card back">
    <div class="social-badges">
      <span class="social-badge tan"></span>
      <span class="social-badge green"></span>
      <span class="social-badge red"></span>
    </div>
    <div class="back-brand">Vine Hollow Excursions</div>
    <p class="tagline">An authentic &amp; boutique wine tour experience</p>
  </section>
</main>
</body>
</html>
```